Business card for Sports Apparel business

DOUBLE SIDED DESIGN
We need business cards for a new sports apparel business. We are developing a protective headband for soccer initially.
Torvalle is focused on designing and developing head protection products to reduce the likelihood of concussion when playing sports. Exploring and understanding medical insights, material science research, current and former players experiences and governing bodies guidelines has allowed Torvalle to develop the safety, style, form and function requirements of a suitable product to bring to market.
Target Market(s)
Mums buying kits for the sons and daughters. Amateur footballers.
Industry/Entity Type
Sporting Good
Contact Information for Business Card
Martin Ashworth - CEO
Mobile: +44 7431589027
Email: martin@torvalle.co.uk
Tel: 0208 5519372
Helena Pargeter - COO
Mob: +44 7385 640117
Email: helena@torvalle.co.uk
Tel: 0208 5519372
Duncan Farrow - CCO
Mob: +44 7564 293081
Email: duncan@torvalle.co.uk
Tel: 0208 5519372
Look and feel
Each slider illustrates characteristics of the customer's brand and the style your logo design should communicate.

```html
<!DOCTYPE html>
<html lang="en">
<head>
<meta charset="utf-8">
<title>Torvalle Business Card</title>
<link href="https://fonts.googleapis.com/css2?family=Open+Sans:wght@300;400;600;700;800&display=swap" rel="stylesheet">
<style>
  :root {
    --brand-blue: #156096;
    --ink-grey: #555a5f;
    --rule-grey: #6a6a6a;
    --card-white: #ffffff;
    --backdrop: #3a3b3d;
  }
  * { margin: 0; padding: 0; box-sizing: border-box; }
  html, body {
    width: 1200px; height: 901px; overflow: hidden;
    background: var(--backdrop);
    font-family: "Open Sans", sans-serif;
  }
  .stage {
    width: 1200px; height: 901px;
    display: flex; flex-direction: column; align-items: center; justify-content: center;
    gap: 40px;
  }
  .card {
    width: 640px; height: 376px; position: relative; overflow: hidden;
    box-shadow: 0 10px 24px rgba(0,0,0,.45);
  }
  .card-front {
    background: var(--brand-blue);
    display: flex; align-items: center; justify-content: center;
  }
  .front-wordmark {
    color: var(--card-white);
    font-weight: 600; font-size: 72px; letter-spacing: 4px;
    text-transform: uppercase;
  }
  .card-back { background: var(--card-white); }
  .back-wordmark {
    position: absolute; right: 44px; top: 58px;
    color: var(--ink-grey);
    font-weight: 600; font-size: 40px; letter-spacing: 2px;
    text-transform: uppercase;
  }
  .person-name {
    position: absolute; left: 44px; top: 206px;
    color: var(--brand-blue); font-weight: 800; font-size: 27px; letter-spacing: .5px;
  }
  .person-role {
    position: absolute; left: 62px; top: 244px;
    color: var(--ink-grey); font-weight: 400; font-size: 15px;
  }
  .divider {
    position: absolute; left: 62px; right: 40px; top: 272px;
    height: 1px; background: var(--rule-grey);
  }
  .contact-list {
    position: absolute; left: 62px; top: 282px; list-style: none;
  }
  .contact-list li {
    display: flex; align-items: center; gap: 8px;
    color: var(--ink-grey); font-weight: 300; font-size: 15.5px; line-height: 26px;
  }
  .contact-list svg, .web-line svg { width: 12px; height: 12px; fill: var(--brand-blue); flex: none; }
  .web-line {
    position: absolute; right: 30px; top: 300px;
    display: flex; align-items: center; gap: 8px;
    color: var(--ink-grey); font-weight: 300; font-size: 15px;
  }
  .accent-bar {
    position: absolute; right: 24px; top: 328px;
    width: 160px; height: 12px; background: var(--brand-blue);
  }
</style>
</head>
<body>
<main class="stage">
  <section class="card card-front">
    <div class="front-wordmark">Torvalle</div>
  </section>

  <section class="card card-back">
    <div class="back-wordmark">Torvalle</div>
    <h1 class="person-name">Martin Ashworth</h1>
    <p class="person-role">CEO</p>
    <div class="divider"></div>
    <ul class="contact-list">
      <li>
        <svg viewBox="0 0 24 24" aria-hidden="true"><path d="M6.6 10.8a15 15 0 0 0 6.6 6.6l2.2-2.2a1 1 0 0 1 1-.25 11.4 11.4 0 0 0 3.6.57 1 1 0 0 1 1 1V20a1 1 0 0 1-1 1A17 17 0 0 1 3 4a1 1 0 0 1 1-1h3.5a1 1 0 0 1 1 1c0 1.25.2 2.45.57 3.6a1 1 0 0 1-.25 1z"/></svg>
        0208 5519372
      </li>
      <li>
        <svg viewBox="0 0 24 24" aria-hidden="true"><path d="M7 1h10a2 2 0 0 1 2 2v18a2 2 0 0 1-2 2H7a2 2 0 0 1-2-2V3a2 2 0 0 1 2-2zm0 3v14h10V4zm5 15.2a1.1 1.1 0 1 0 0 2.2 1.1 1.1 0 0 0 0-2.2z"/></svg>
        +44 7431589027
      </li>
      <li>
        <svg viewBox="0 0 24 24" aria-hidden="true"><path d="M2 5h20v14H2zm2 2v.4l8 5.2 8-5.2V7zm0 2.8V17h16V9.8l-8 5.2z"/></svg>
        martin@torvalle.co.uk
      </li>
    </ul>
    <div class="web-line">
      <svg viewBox="0 0 24 24" aria-hidden="true"><circle cx="12" cy="12" r="10"/></svg>
      www.torvalle.co.uk
    </div>
    <div class="accent-bar"></div>
  </section>
</main>
</body>
</html>
```